Fixwell and guard Word doc project

Fixwell & Guard are an established home appliance repair and warranty provider looking to rebrand the letters sent to our customers with a new and fresh design.
Please refer to our website for our colour scheme and logo which we are not looking to change:
www.fixwellandguard.co.uk
The letters which we are looking to have redesigned are:
Welcome letters / confirmation paperwork
Basic letter template
Welcome letters:
Page 1 – Opening / Welcome
Page 2 – Plan documentation details
Page 3 & 4 – Terms & Conditions
We can provide a copy of our current welcome / confirmation letters but as we are looking for full redesign, we are looking to steer away from what we have been using historically.
We will be running further projects and we are looking to use the same designer which we pick from this competition so please consider this when submitting your designs.
UPDATE - 01/11/23
An example of our current Welcome documentation has been uploaded for the purpose of example of the placement of the content. As per the brief, we are not looking for a similar design but purely uploading the current documentation to give you an idea of what we are currently using.
Look and feel
Each slider illustrates characteristics of the customer's brand and the style your logo design should communicate.

```html
<!DOCTYPE html>
<html lang="en">
<head>
<meta charset="utf-8">
<title>Fixwell &amp; Guard – Welcome Pack</title>
<link href="https://fonts.googleapis.com/css2?family=Open+Sans:wght@400;600;700&family=Montserrat:wght@600;700&display=swap" rel="stylesheet">
<style>
:root{
  --blue:#1a2fd6;
  --blue-dark:#0f1fa8;
  --green:#1f9a3c;
  --green-light:#4cc35a;
  --ink:#222;
  --muted:#555;
  --white:#fff;
}
*{box-sizing:border-box;margin:0;padding:0}
html,body{width:1200px;height:5382px;overflow:hidden;background:#fff}
body{position:relative;font-family:"Open Sans",Arial,sans-serif;color:var(--ink)}
.page{position:absolute;left:161px;width:872px;height:1238px;background:var(--white);box-shadow:4px 6px 14px rgba(0,0,0,.25);overflow:hidden}
.page svg.deco{position:absolute;left:0;top:0}
.brand-circle{position:absolute;border-radius:50%;background:var(--white);display:flex;align-items:center;justify-content:center;text-align:center;color:var(--blue);font-weight:700;letter-spacing:.04em}
.footer-bar{position:absolute;left:0;background:var(--blue);color:var(--white);display:flex;align-items:center;justify-content:center}
.reg-note{font-size:8px;color:var(--white)}

/* page 1 */
.p1 .recipient{position:absolute;left:81px;top:400px;color:var(--white);font-size:12px;line-height:18px}
.p1 .recipient strong{display:block;font-size:13px;margin-bottom:10px}
.p1 .sender{position:absolute;right:118px;top:558px;text-align:right;font-size:12px;line-height:17px}
.p1 .sender .co{color:var(--blue);font-size:13px}
.p1 .date{position:absolute;right:118px;top:645px;font-weight:700;font-size:12.5px}
.p1 .letter{position:absolute;left:86px;top:715px;width:666px;font-size:12.5px;line-height:18px}
.p1 .letter p{margin-bottom:16px}
.p1 .letter .hl{color:var(--green)}
.signature{width:190px;height:50px;margin:8px 0 20px;background:linear-gradient(90deg,#e7e7e7,#f5f5f5)}
.p1 .contact{font-size:21px;gap:40px}
.p1 .contact span{display:flex;align-items:center;gap:8px}

/* headers pages 2-4 */
.header-title{position:absolute;left:65px;color:var(--white);font-family:Montserrat,Arial,sans-serif;font-weight:700;font-size:24px}
.header-title .accent{color:var(--green-light)}

/* page 2 */
.fields{position:absolute;left:63px;top:198px;width:720px;display:grid;grid-template-columns:237px 273px 210px;row-gap:30px}
.field .label{color:var(--blue);font-weight:700;font-size:13px}
.field .label.g{color:var(--green)}
.field .value{font-size:12px;margin-top:4px}
.appliances{position:absolute;left:63px;top:470px;width:710px;border-collapse:collapse;font-size:12px}
.appliances th{text-align:left;color:var(--blue);font-size:13.5px;padding:10px 0;border-top:1.5px solid #8ea0ff;border-bottom:1.5px solid #8ea0ff}
.appliances td{padding:10px 0 11px}
.detach{position:absolute;left:65px;top:830px;width:701px;text-align:center;font-weight:700;font-size:11.5px}
.guarantee{position:absolute;left:65px;top:855px;width:701px;height:236px;border:1px solid #999;padding:12px 14px;font-size:10.5px;line-height:14px}
.guarantee h3{font-size:15px;margin-bottom:14px}
.guarantee .mark{position:absolute;right:14px;top:12px;display:flex;align-items:center;gap:6px;font-weight:700;font-size:13px}
.guarantee .mark i{width:18px;height:18px;border-radius:50%;background:#111;display:block}
.guarantee ul{list-style:none}
.guarantee li{position:relative;padding-left:24px;margin-bottom:7px}
.guarantee li::before{content:"➤";position:absolute;left:0;font-size:9px}
.guarantee li.sub{padding-left:30px}
.guarantee li.sub::before{content:"-";left:24px}

/* terms */
.terms{position:absolute;left:63px;width:712px;display:flex;flex-direction:column;justify-content:space-between;font-size:7.4px;line-height:10px;color:var(--ink)}
.terms h4{color:var(--blue);font-size:10.5px;line-height:13px;margin-bottom:2px}
.terms p{margin-bottom:2px}
.cont-note{position:absolute;right:96px;font-size:10px;color:var(--blue)}
</style>
</head>
<body>

<!-- PAGE 1 -->
<section class="page p1" style="top:104px">
  <svg class="deco" width="872" height="1238" viewBox="0 0 872 1238">
    <polygon points="0,0 872,0 872,90 505,560 0,560" fill="var(--blue)"/>
    <polygon points="0,0 240,0 120,150 0,140" fill="#2b45e8" opacity=".55"/>
    <polygon points="90,0 330,0 200,170" fill="#0e22b8" opacity=".35"/>
    <polygon points="810,560 872,540 872,1140 810,1140" fill="var(--green)"/>
    <polygon points="835,700 872,680 872,900 835,920" fill="var(--green-light)"/>
    <polygon points="0,1085 120,1050 872,1020 872,1145 0,1145" fill="var(--green)"/>
    <polygon points="0,1145 0,1120 260,1080 380,1145" fill="var(--green-light)" opacity=".7"/>
  </svg>
  <div class="brand-circle" style="left:465px;top:114px;width:314px;height:314px;border:9px solid var(--blue);font-size:22px">FIXWELL &amp; GUARD</div>

  <div class="recipient"><strong>Title Initial Family Name</strong>Address 1<br>Address 2<br>Town<br>County<br>Postcode</div>
  <div class="sender"><div class="co">Fixwell &amp; Guard LTD</div>Harbour House<br>14 Quay Road, Seaford BN9 2AB</div>
  <div class="date">02 November 2023</div>

  <div class="letter">
    <p>Dear Title Family Name,</p>
    <p>Thank you for choosing Fixwell &amp; Guard Ltd. You can now put your mind at ease knowing that your appliance(s) are protected.</p>
    <p>We have enclosed your plan documents. Please read through your plan documents to ensure all the information is correct. If you wish to update or change any of the information, please contact us on <span class="hl">FREEPHONE 0800 123 4567.</span></p>
    <p>To ensure that there are no gaps in your cover, please contact us should you require an update of your payment details or if you change bank. We will also ensure that your plan is automatically renewed.</p>
    <p>Are you stuck? Get in touch…<br>If you need help: from booking a repair, to adding additional appliances to your plan. Call us on FREEPHONE 0800 123 4567. Rest assured that your appliance(s) are in the correct hands. We look after them, so you don't have to!</p>
    <p>Yours sincerely,</p>
    <div class="signature" role="img" aria-label="Handwritten signature"></div>
    <p style="line-height:16px">Maya Orwell<br>Customer Service Manager<br>Fixwell &amp; Guard Ltd</p>
  </div>

  <div class="reg-note" style="position:absolute;right:80px;top:1121px">Fixwell &amp; Guard Ltd is a registered company in England under Registration Number 071148</div>
  <div class="footer-bar contact" style="top:1148px;width:810px;height:46px">
    <span><svg width="18" height="18" viewBox="0 0 24 24"><path d="M6.6 10.8a15 15 0 006.6 6.6l2.2-2.2a1 1 0 011-.25 11.4 11.4 0 003.6.57 1 1 0 011 1V20a1 1 0 01-1 1A17 17 0 013 4a1 1 0 011-1h3.5a1 1 0 011 1c0 1.25.2 2.45.57 3.570a1 1 0 01-.25 1z" fill="#fff"/></svg>0800 123 4567</span>
    <span><svg width="18" height="18" viewBox="0 0 24 24"><circle cx="12" cy="12" r="9.5" fill="none" stroke="#fff" stroke-width="2"/><path d="M2.5 12h19M12 2.5c3 3 3 16 0 19M12 2.5c-3 3-3 16 0 19" fill="none" stroke="#fff" stroke-width="1.6"/></svg>www.fixwellandguard.co.uk</span>
  </div>
</section>

<!-- PAGE 2 -->
<section class="page" style="top:1388px">
  <svg class="deco" width="872" height="1238" viewBox="0 0 872 1238">
    <rect width="872" height="160" fill="var(--blue)"/>
    <polygon points="0,0 200,0 90,110 0,100" fill="#2b45e8" opacity=".55"/>
    <polygon points="810,160 872,140 872,1170 810,1170" fill="var(--green)"/>
    <polygon points="835,700 872,680 872,1000 835,1020" fill="var(--green-light)"/>
    <polygon points="660,1170 872,1080 872,1170" fill="var(--green)"/>
  </svg>
  <div class="brand-circle" style="left:685px;top:18px;width:146px;height:146px;border:6px solid var(--blue);font-size:11px">FIXWELL &amp; GUARD</div>
  <h1 class="header-title" style="top:82px">YOUR COVER <span class="accent">DETAILS</span></h1>

  <div class="fields">
    <div class="field"><div class="label">Cover Start Date</div><div class="value">Plan Start Date</div></div>
    <div class="field"><div class="label g">Payment Charge Date 1</div><div class="value">Plan Start Date</div></div>
    <div class="field"><div class="label g">Monthly Bank Payment Amount</div><div class="value">£Paid Today</div></div>
    <div class="field"><div class="label">Cover Renewal Date</div><div class="value">Plan End Date</div></div>
    <div class="field"><div class="label g">Instalment Type</div><div class="value">Plan Frequency</div></div>
    <div class="field"><div class="label g">Total Cost of plan</div><div class="value">£Pay Total</div></div>
    <div class="field"><div class="label">Service Plan ID Number</div><div class="value">Plan ID</div></div>
    <div class="field"><div class="label g">Plan Length</div><div class="value">Plan Length</div></div>
  </div>

  <table class="appliances">
    <thead><tr><th style="width:237px">Appliance Type</th><th style="width:273px">Manufacture</th><th>Appliance Age</th></tr></thead>
    <tbody>
      <tr><td>Appliance 1</td><td>Manufacturer 1</td><td></td></tr>
      <tr><td>Appliance 2</td><td>Manufacturer 2</td><td></td></tr>
      <tr><td>Appliance 3</td><td>Manufacturer 3</td><td></td></tr>
      <tr><td>Appliance 4</td><td>Manufacturer 4</td><td></td></tr>
      <tr><td>Appliance 5</td><td>Manufacturer 5</td><td></td></tr>
      <tr><td>Appliance 6</td><td>Manufacturer 6</td><td></td></tr>
    </tbody>
  </table>

  <div class="detach">This Guarantee should be detached and retained by the payer.</div>
  <div class="guarantee">
    <h3>The Bank Payment Guarantee</h3>
    <div class="mark"><i></i>Bank Payment</div>
    <ul>
      <li>This Guarantee is offered by all banks and building societies that accept instructions to pay by Bank Payment.</li>
      <li>If there are any changes to the amount, date or frequency of your Bank Payment, Fixwell &amp; Guard Ltd will notify you 10 working days in advance of your account being debited or as otherwise agreed. If you request Fixwell &amp; Guard Ltd to collect a payment, confirmation of the amount and date will be given to you at the time of the request.</li>
      <li>If an error is made in the payment of your Bank Payment by Fixwell &amp; Guard Ltd or your bank or building society, you are entitled to a full and immediate refund of the amount paid from your bank or building society.</li>
      <li class="sub">If you receive a refund you are not entitled to, you must pay it back when Fixwell &amp; Guard Ltd asks you to.</li>
      <li>You can cancel a Bank Payment at any time by simply contacting your bank or building society. Written confirmation may be required. Please also notify us.</li>
    </ul>
  </div>
  <div class="footer-bar" style="top:1170px;width:810px;height:26px"><span class="reg-note">Fixwell &amp; Guard Ltd is a registered company in England under Registration Number 071148</span></div>
</section>

<!-- PAGE 3 -->
<section class="page" style="top:2676px">
  <svg class="deco" width="872" height="1238" viewBox="0 0 872 1238">
    <rect width="872" height="132" fill="var(--blue)"/>
    <polygon points="0,0 200,0 90,110 0,100" fill="#2b45e8" opacity=".55"/>
    <polygon points="810,132 872,112 872,1175 810,1175" fill="var(--green)"/>
    <polygon points="835,600 872,580 872,900 835,920" fill="var(--green-light)"/>
    <polygon points="560,1175 872,1100 872,1175" fill="var(--green)"/>
  </svg>
  <div class="brand-circle" style="left:700px;top:10px;width:130px;height:130px;border:6px solid var(--blue);font-size:10px">FIXWELL &amp; GUARD</div>
  <h1 class="header-title" style="top:78px">Plan Terms <span class="accent">and Conditions</span></h1>
  <div class="terms" style="top:146px;height:992px">
    <div>
      <p>Your policy start date is shown on your plan schedule, for all cases where a plan has started after the expiry of your manufacturer's guarantee. It is important for your benefit and protection that you read these terms and conditions. These and your certificate, and any changes we notify you about (at renewal or otherwise), form your agreement with us. We intend to rely on the terms and conditions set out in this document. Full protection will start thirty days after your application is processed; during the first thirty days you will be covered for technical assistance only, as any faults reported within the first thirty days will be considered pre-existing. After this initial period you will be entitled to telephone assistance and full engineering assistance as per your terms and conditions.</p>
    </div>
    <div><h4>Definitions</h4>
      <p>Plan: this contract of services. Product: the appliance(s) protected by this plan, as shown on your plan schedule. We/us/our: Fixwell &amp; Guard Ltd, the provider of the plan. You/your: the person named on your plan schedule. Your certificate: the personalised section of your plan documentation, sent to you once you have taken out a plan or at renewal.</p></div>
    <div><h4>Contract of services</h4>
      <p>This plan is not categorised as an insurance product and therefore insurance regulation does not apply. This plan is a contract of services and is governed by the laws of England and Wales and the consumer regulations that apply to contracts of this type.</p></div>
    <div><h4>Important conditions and your obligations</h4>
      <p>The following conditions apply to this plan:<br>• You must provide us with all relevant information that we request when you apply for the plan. All information you give must not be false, exaggerated or misleading.<br>• Your product must have been installed, maintained and used in accordance with the manufacturer's instructions.<br>• Your product must be owned by you and kept only for domestic use.<br>• Your product must be used in a private home, solely occupied by your household (at the address you gave to us).<br>• Your product must be easily accessible and meet all relevant safety standards and be safe to work on.<br>• Your product must not contain any content that may be illegal, and if we find any such content we reserve the right to inform the relevant authorities.</p></div>
    <div><h4>Your obligations</h4>
      <p>You must arrange any work required to make your product accessible and compliant with all relevant safety standards and safe to work on, and you will be responsible for carrying out such work before a repair can be booked. Where you have requested services from us, you must also notify us if such work is required, let us know when it has been completed and provide us with the relevant certification where applicable. We won't provide our services until you have fulfilled these obligations. If you do not comply with the conditions and the eligibility requirements above, or do not fulfil your obligations, we will end your plan.</p></div>
    <div><h4>What this plan includes</h4>
      <p>Breakdown: if your product suffers a mechanical or electrical breakdown after the end of the manufacturer's parts and labour guarantee period, our customer services team will try to resolve the problem over the telephone. If we are unable to resolve the issue, we will, at our discretion, decide whether to approve a repair. Where a repair is approved, we will then authorise an engineer to carry out your repair, or we may also (at our option) decide to replace or pay the cost of replacing your product, in each case subject to these terms and conditions.</p></div>
    <div><h4>How to request repair</h4>
      <p>To request a repair please contact us as soon as possible by telephone. The telephone number will be shown on your plan documents and on our website.</p></div>
    <div><h4>Limits of the plan</h4>
      <p>There is no limit to the number of repairs you can request under your plan during the plan period, subject to these terms and conditions.</p></div>
    <div><h4>Repairs information</h4>
      <p>Information we may require: you must give us all information we need to register your repair request. You should send any requested documents to the address in 'Customer services details' below, including proof of purchase where asked.</p></div>
    <div><h4>Important information about repairs</h4>
      <p>Only engineers approved by us are authorised to carry out repairs under this plan, unless we agree otherwise in advance. Repairs will be carried out within the repairer's normal working hours (which are at least 9am to 5pm, Monday to Friday) on a date agreed with you. Please have your plan documentation to hand when the repairer arrives. If your product breaks down, you must take reasonable steps to limit damage, e.g. stop using it if this is likely to cause further damage.</p></div>
    <div><h4>Replacements</h4>
      <p>If a repair is approved, we may (at our option) decide to replace your product with a new product of the same or similar technical specification, or to pay the cost of replacing it.</p></div>
    <div><h4>What happens if your product is replaced?</h4>
      <p>If we decide to replace your product any unpaid fee for the current plan period will become due. No fee paid will be refunded. When your product is replaced (or you have received our contribution) your plan will continue on the new appliance with twelve months of cover, or the remainder of your plan period, whichever is shorter. Product disposal and delivery, installation and other costs: if the product is taken or sent away from your home for repair and is then replaced, the original product will become our property and we will dispose of it. If your product remains in your home but is replaced, you will be responsible for disposing of it at your own cost. We do not cover the costs of installation for integrated, built-in or freestanding appliances, nor do we cover the costs for removal of previous appliances.</p></div>
    <div><h4>What happens if we decide not to repair or replace?</h4>
      <p>If we do decide not to approve a repair or replacement request which would otherwise fall within the terms of your plan, we will inform you. All fee payments you have made in the current period of your plan will be refunded and your plan will end immediately. No further amounts will be payable. We'll confirm this in writing to the last address you gave us.</p></div>
    <div><h4>General exclusions</h4>
      <p>Unless they are listed under the 'What this plan includes' section, the following are excluded from the plan, and we will not pay for repairs which relate to:<br>• Damage during delivery, installation or transportation of the product by a third party who is not our agent.<br>• Any appliance over ten years of age.<br>• Any breakdown covered by any manufacturer's, supplier's or repairer's guarantee or warranty on a product.<br>• Replacement or recall of the product (or any part) by a supplier or the manufacturer.<br>• Modifying or making a product comply with legislation, work on the product that is only required due to legislation changes or making it safely accessible.<br>• Your failure to follow the manufacturer's instructions.<br>• Any problem with the supply of electricity, gas, water, broadband or broadcast content.<br>• Routine maintenance, cleaning, servicing and re-gassing.<br>• Repairs carried out outside of your country of residence.<br>• Costs or loss arising from not being able to use your product (e.g. hiring a replacement) or incidental costs caused by breakdown or repair (e.g. costs to remove or reinstate built-in or fitted equipment).</p></div>
  </div>
  <div class="cont-note" style="top:1150px">The Terms and Conditions are continued on the reverse side.</div>
  <div class="footer-bar" style="top:1175px;width:810px;height:26px"><span class="reg-note">Fixwell &amp; Guard Ltd is a registered company in England under Registration Number 071148</span></div>
</section>

<!-- PAGE 4 -->
<section class="page" style="top:3955px">
  <svg class="deco" width="872" height="1238" viewBox="0 0 872 1238">
    <rect width="872" height="132" fill="var(--blue)"/>
    <polygon points="0,0 200,0 90,110 0,100" fill="#2b45e8" opacity=".55"/>
    <polygon points="810,132 872,112 872,1170 810,1170" fill="var(--green)"/>
    <polygon points="835,600 872,580 872,900 835,920" fill="var(--green-light)"/>
    <polygon points="560,1170 872,1095 872,1170" fill="var(--green)"/>
  </svg>
  <div class="brand-circle" style="left:700px;top:10px;width:130px;height:130px;border:6px solid var(--blue);font-size:10px">FIXWELL &amp; GUARD</div>
  <div class="terms" style="top:146px;height:992px">
    <div>
      <p>• Damage to any other property or possessions unless it is our fault.<br>• Cosmetic damage such as damage to paintwork, dents or scratches.<br>• Any loss, damage or impairment to functionality caused by theft, attempted theft, neglect, deliberate damage or damage caused by animals, plants or insects.<br>• Any loss, damage or impairment to functionality caused by earthquake, flood, lightning, fire, wind, humidity, weather conditions, soil spray, smoke or other natural events or catastrophes, abnormally high or low temperatures, plumbing problems, corrosion, chemical exposure, radiation, explosion, sabotage, terrorism, insurrection, riot, civil commotion, rebellion, man-made events or catastrophes or technological hazards.<br>• Any appliance not registered under the plan.<br>• Repairs, maintenance work, or use of spare parts, where not approved by us.<br>• Damage to ceramic or glass surfaces.<br>• Commercial or business use including use by charities, not-for-profit organisations, local government, or any other such similar organisations (unless we agree in writing beforehand).<br>• Fraud or attempted fraud, or where the condition of the product is not consistent with the request you have made.<br>• The cost of replacing any accessories including external hoses, batteries, rechargeable batteries, power cells, light bulbs, fuses, filters and related starter components, attachments, cabinets, doors and cable parts, plugs, light covers, grills, removable parts, glass and enamel parts, seals, gaskets and rubber parts.<br>• Any cost that arises from the failure or degradation of an appliance that has been exposed to or used with products that are not recommended by the manufacturer.<br>• Damage caused by, or arising from, accident.</p>
    </div>
    <div><h4>Special exclusions</h4>
      <p>In addition to the 'General exclusions' above, the following are excluded from the plan, and we will not pay for repairs which relate to:<br>• Add-ons and peripherals connected to your product, and any software, data or settings stored on it.</p></div>
    <div><h4>Paying your fees</h4>
      <p>1. If you pay the fees (inclusive of all applicable taxes) on an instalment basis, you must make regular payments in accordance with the 'Payments schedule' set out in your plan documentation. If we are unable to collect a payment from your bank we may attempt to request payment again unless you advise us otherwise. When you have paid your instalments payments for the number of consecutive payment periods shown in the 'Payments schedule', if the initial plan period has not yet expired, no further payment will be taken for the remainder of the initial plan period.<br>2. If instead you choose to pay all the fees for the period in advance in one payment, you must pay this amount (inclusive of all applicable taxes) before the plan will start.<br>3. We may use a collection agency to recover any amount owing to us.<br>4. If you do not pay for your plan on time, it will be suspended from the due date. Any requests for repairs made during this period will not be considered for approval unless payment is received.</p></div>
    <div><h4>Duration and renewal of your plan</h4>
      <p>1. The initial plan period begins on the start date and continues until the expiry date as specified in your certificate (unless ended in accordance with these terms and conditions).<br>2. Before your plan ends, we will write to you about renewing. Your renewal notice will show the amount to pay. The fee payable may increase at renewal.<br>3. A cooling-off period (lasting fourteen days from renewal of the plan) applies at the renewal of your plan.<br>4. We reserve the right not to offer you a renewal on your plan.</p></div>
    <div><h4>Cancellation and ending of the plan</h4>
      <p>1. The cooling-off period is the fourteen day period from receipt of your documentation or from the plan start date, whichever is later.<br>2. If you change your mind during the cooling-off period, you can cancel your plan and we'll refund any fee paid.<br>3. If your plan automatically ends or is cancelled by us, these rights do not apply (see 'Our right to cancel your plan or bring it to an end' below).</p></div>
    <div><h4>After the cooling-off period</h4>
      <p>You may cancel the plan up to the day before the renewal date. We will refund the unused portion of the fee you have paid, less any costs of approved repairs carried out in the current plan period. If you have received a repair, no refund will be given and you will have to pay the cost of the repair. This will be capped at the plan fee for the remaining term.</p></div>
    <div><h4>How to cancel</h4>
      <p>If you wish to cancel your plan, please contact us on 0800 123 4567 during our customer services hours of 9am to 5.30pm. You can also cancel by writing to us at the address specified in 'Customer services details' below. If you do wish to cancel, please contact us directly to avoid any miscommunication regarding outstanding payments.</p></div>
    <div><h4>Customer services details</h4>
      <p>For customer services call 0800 123 4567, write to us at Fixwell &amp; Guard Ltd, Harbour House, 14 Quay Road, Seaford BN9 2AB, or email us by clicking on 'contact us' on our website: www.fixwellandguard.co.uk. Calls to 0800 numbers are free. Calls may be recorded and monitored for quality and training purposes.</p></div>
    <div><h4>Our right to cancel your plan or bring it to an end</h4>
      <p>1. If you fail to comply with certain conditions and obligations (see 'Important conditions and your obligations' above) we may bring your plan to an end and we won't provide any further services to you under the plan.<br>2. We reserve the right to cancel your plan by giving you fourteen days' notice.<br>3. In such case, we'll confirm any such ending or cancellation of the plan in writing to the last address you gave us.</p></div>
    <div><h4>How to complain</h4>
      <p>If you wish to complain or you are unhappy with the service provided, please contact our customer services team (see 'Customer services details' above). Transferring your plan to a new owner: with our permission you may transfer your plan to a new owner of the equipment by giving us written details in writing. Your plan cannot be transferred to any other equipment.</p></div>
    <div><h4>Changes to these terms and conditions</h4>
      <p>We can, at any time and after taking a fair and reasonable view, modify or replace these terms and conditions in order to:<br>• Comply with the law, regulations, industry guidance or codes of practice.<br>• Rectify errors or ambiguities; and<br>• Rectify changes in the scope or nature of the protection provided to you. We will give you fourteen days' written notice of any change that could have a material effect on your rights or obligations. The new terms and conditions will take effect from the date specified in the notice.</p></div>
    <div><h4>Important data protection information</h4>
      <p>Fixwell &amp; Guard Ltd and its business partners will use your information (which you or others have provided to us) to provide the requested services and for administration (including the recovery of any amounts owing, where applicable), marketing, market research, customer surveys, regulatory reporting, to check and verify your identity and analytics and testing purposes. Your information may also be shared with selected companies acting on our behalf. We, along with our business partners and third parties, may use your information to tell you about any offers, products or services which may be of interest to you. You may therefore be contacted by mail, telephone, email and/or other electronic messaging services unless you have asked not to be. You may request a copy of your data. Should your personal details change, if you wish to change your marketing preferences or if you wish to opt out of receiving marketing information, please let us know by writing to the Data Protection Officer at our registered office.</p></div>
    <div><h4>Exclusion of third party rights</h4>
      <p>This plan is only for your benefit. No rights or benefits will be given to any other third party under the plan.</p></div>
    <div><h4>Governing law and statutory rights</h4>
      <p>We will communicate with you in English and English law will apply unless we agree otherwise with you. Nothing in the conditions will reduce or affect your statutory rights. For further information about your statutory rights contact your local consumer advice service.</p></div>
    <div><h4>Company information</h4>
      <p>This plan is provided by Fixwell &amp; Guard Ltd. Registered in England and Wales. Company No. 071148. Registered office: Harbour House, 14 Quay Road, Seaford BN9 2AB.</p></div>
  </div>
  <div class="footer-bar" style="top:1170px;width:810px;height:26px"><span class="reg-note">Fixwell &amp; Guard Ltd is a registered company in England under Registration Number 071148</span></div>
</section>

</body>
</html>
```